New Innovative Counselling and psychotherapy Service needs Business Card design

Keep it simple and professional. On one side, just company name and logo (perhaps in all blue) and maybe a tag line.

On other side (all white) my name and Qualifications in centre

Industry/Entity Type

Health And Wellness

Contact Information for Business Card

Dara Whelby
Counsellor & Psychotherapist
BSc (Psychol.), BA, Dip. (Couns. & Psych.), PG.Cert (CBT), FGTrK, ONRE

I will also require Mobile no, Email and web site address of which I'll pass on to final designer.

Font styles to use
Sans Serif

Requirements
Must have
• My Logo Only and please use the colours in logo that is in it.
Should not have
• Any other images

```html
<!DOCTYPE html>
<html lang="en">
<head>
<meta charset="utf-8">
<title>Thrive Crescent – Business Card</title>
<link rel="stylesheet" href="https://fonts.googleapis.com/css2?family=Roboto:wght@300;400;700&display=swap">
<style>
  :root {
    --backdrop: #e8e9eb;
    --brand-blue: #4fb6ea;
    --deep-blue: #3b9fd8;
    --leaf-green: #7cc454;
    --card-white: #f7f7f7;
    --ink: #2a2a2a;
    --soft-ink: #444;
  }
  * { box-sizing: border-box; margin: 0; padding: 0; }
  html, body {
    width: 1200px; height: 726px; overflow: hidden;
    background: var(--backdrop);
    font-family: "Roboto", Arial, sans-serif;
  }
  .canvas {
    position: relative; width: 1200px; height: 726px;
    display: flex; align-items: center; justify-content: center; gap: 50px;
  }
  .card {
    position: relative; width: 525px; height: 300px;
    box-shadow: 0 2px 6px rgba(0,0,0,.12);
    overflow: hidden;
  }
  /* Front */
  .card--front {
    background: var(--brand-blue);
    display: flex; flex-direction: column; align-items: center; justify-content: center;
    color: #fff;
  }
  .brand { display: flex; align-items: center; gap: 14px; }
  .brand__dot { width: 46px; height: 46px; border-radius: 50%; flex: none; }
  .card--front .brand__dot { background: #fff; }
  .brand__name { font-weight: 300; font-size: 40px; letter-spacing: .5px; line-height: 1; }
  .tagline {
    margin-top: 10px; margin-left: 60px;
    font-size: 13px; letter-spacing: 6px; font-weight: 400;
  }
  /* Back */
  .card--back { background: var(--card-white); color: var(--ink); }
  .card--back .brand { position: absolute; left: 40px; top: 62px; }
  .card--back .brand__dot { background: var(--deep-blue); }
  .card--back .brand__name { color: var(--ink); font-size: 38px; }
  .person { position: absolute; left: 40px; top: 150px; }
  .person__name { color: var(--deep-blue); font-weight: 700; font-size: 21px; line-height: 1.1; }
  .person__role, .person__quals { font-size: 11.5px; color: var(--soft-ink); line-height: 1.35; }
  .contacts { position: absolute; left: 50px; top: 218px; list-style: none; }
  .contacts li { display: flex; align-items: center; gap: 12px; font-size: 13px; color: var(--ink); line-height: 1.45; }
  .contacts svg { width: 12px; height: 12px; flex: none; }
  .stripe { position: absolute; left: 0; right: 0; bottom: 0; height: 7px; display: flex; }
  .stripe__blue { flex: 1; background: var(--brand-blue); }
  .stripe__green { flex: 1; background: var(--leaf-green); }
</style>
</head>
<body>
<main class="canvas">
  <section class="card card--front" aria-label="Card front">
    <div class="brand">
      <span class="brand__dot"></span>
      <span class="brand__name">Thrive Crescent</span>
    </div>
    <p class="tagline">A tag line goes here</p>
  </section>

  <section class="card card--back" aria-label="Card back">
    <div class="brand">
      <span class="brand__dot"></span>
      <span class="brand__name">Thrive Crescent</span>
    </div>
    <div class="person">
      <h1 class="person__name">Dara Whelby</h1>
      <p class="person__role">Counsellor &amp; Psychotherapist</p>
      <p class="person__quals">BSc (Psychol.), BA, Dip. (Couns. &amp; Psych.), PG.Cert (CBT), FGTrK, ONRE</p>
    </div>
    <ul class="contacts">
      <li>
        <svg viewBox="0 0 12 12" aria-hidden="true"><path fill="#4aa27a" d="M1 4c0-1.5 2-3 5-3s5 1.5 5 3l-2.5 1L7.5 3.5h-3L3.5 5 1 4zM2.5 6h7l1 5h-9z"/></svg>
        <span>0123 456 7801</span>
      </li>
      <li>
        <svg viewBox="0 0 12 12" aria-hidden="true"><rect x="0.5" y="2" width="11" height="8" fill="#4aa27a"/><path d="M0.5 2l5.5 4.5L11.5 2" fill="none" stroke="#fff" stroke-width="1"/></svg>
        <span>dara.w@ThriveCrescent.com</span>
      </li>
      <li>
        <svg viewBox="0 0 12 12" aria-hidden="true"><circle cx="6" cy="6" r="5.3" fill="#4aa27a"/><path d="M0.7 6h10.6M6 0.7v10.6M6 0.7c-3 3-3 7.6 0 10.6M6 0.7c3 3 3 7.6 0 10.6" fill="none" stroke="#fff" stroke-width=".7"/></svg>
        <span>www.ThriveCrescent.com</span>
      </li>
    </ul>
    <div class="stripe"><span class="stripe__blue"></span><span class="stripe__green"></span></div>
  </section>
</main>
</body>
</html>
```